Business card design for a dynamic IT consulting company

We need a business card design for a young firm, specialized in the Telecommunications/Consulting industry. The name of the company is Quindor and Partners Business Consulting Ltd. (Short name: Quindor and Partnes)
Quindor = solve read reverse, so we aim to be uncomplicated and solution-oriented. The small pipe in our logo is also related to the word solve. So we need a new business card design, which is simple, eye catching and something non traditional (I would probably prefer a square shaped design rather than a rectangle, but open for suggestions). Attached our logo.

Target Market(s)

Usually our customers are Tier1 Telecoms providers (Q-Netra, Palorix, etc) and their executives.

Industry/Entity Type

Business

Contact Information for Business Card

Name: Bence Tolnavari
Email: b.tolnavari@quindor.hu
Web: www.quindor.hu
Mobile: +36 30 518 2769
Title: Managing Director

Optional:
Company name: Quindor and Partners Ltd.
Address: 1087 Budapest, Tolvenka str. 28/C, Hungary

Font styles to use
Other font styles liked:
• helveticaneue_medium, Prime Regular are used now.

Colors

Designer to choose colors to be used in the design.

Requirements
Must have
• I would like to have a 2 sided design.
Nice to have
• I thought if we make the logo a bit bigger (without the company name), that could go to the back with the company name below. I though, if the pipe in the logo is somehow touchable on the business card, would be nice and unique.

```html
<!DOCTYPE html>
<html lang="en">
<head>
<meta charset="utf-8">
<title>Quindor and Partners – Business Card</title>
<link rel="stylesheet" href="https://fonts.googleapis.com/css2?family=Exo+2:wght@500&family=Work+Sans:wght@400;500&display=swap">
<style>
  :root {
    --backdrop: #2f2926;
    --card: #1b1b1d;
    --card-front: #161617;
    --edge: #1f8fc9;
    --cyan: #1ea4e0;
    --magenta: #b62f9a;
    --white: #f1f1f1;
    --silver: #9a9a9c;
  }
  * { margin: 0; padding: 0; box-sizing: border-box; }
  html, body { width: 1200px; height: 715px; overflow: hidden; }
  body {
    background: var(--backdrop);
    font-family: "Work Sans", Arial, sans-serif;
    position: relative;
  }
  .card {
    position: absolute;
    top: 205px;
    width: 520px;
    height: 300px;
    border-radius: 6px;
  }
  .card-front {
    left: 50px;
    background: var(--card-front);
    border: 4px solid var(--edge);
    display: flex;
    align-items: center;
    justify-content: center;
    gap: 14px;
  }
  .brand-mark {
    width: 26px;
    height: 26px;
    background: var(--silver);
  }
  .brand-name {
    font-weight: 500;
    font-size: 34px;
    color: var(--silver);
    letter-spacing: 0.5px;
  }
  .card-back {
    left: 630px;
    background: var(--card);
  }
  .back-brand {
    position: absolute;
    left: 34px;
    top: 128px;
    display: flex;
    align-items: center;
    gap: 10px;
  }
  .back-brand .brand-mark { width: 20px; height: 20px; background: var(--cyan); }
  .back-brand .brand-name { font-size: 26px; color: var(--white); }
  .divider {
    position: absolute;
    left: 228px;
    top: 62px;
    width: 2px;
    height: 186px;
    background: var(--magenta);
  }
  .contact {
    position: absolute;
    left: 248px;
    top: 62px;
    color: var(--white);
    font-size: 13.5px;
    line-height: 1.35;
  }
  .person-name {
    font-family: "Exo 2", Arial, sans-serif;
    font-weight: 500;
    font-size: 21px;
    letter-spacing: 1.5px;
    color: var(--cyan);
    text-transform: uppercase;
  }
  .person-title { margin-bottom: 10px; }
  .company {
    font-family: "Exo 2", Arial, sans-serif;
    font-weight: 500;
    font-size: 14px;
    letter-spacing: 0.8px;
    color: var(--cyan);
    text-transform: uppercase;
  }
  .address { margin-bottom: 8px; }
  .line { display: flex; align-items: center; gap: 8px; }
  .line svg { width: 11px; height: 11px; flex: none; }
</style>
</head>
<body>
  <section class="card card-front" aria-label="Card front">
    <span class="brand-mark"></span>
    <span class="brand-name">Quindor &amp; Partners</span>
  </section>

  <section class="card card-back" aria-label="Card back">
    <div class="back-brand">
      <span class="brand-mark"></span>
      <span class="brand-name">Quindor</span>
    </div>
    <div class="divider"></div>
    <div class="contact">
      <p class="person-name">Bence Tolnavari</p>
      <p class="person-title">Managing Director</p>
      <p class="company">Quindor and Partners Ltd.</p>
      <p class="address">1087 Budapest, Tolvenka<br>str. 28/C, Hungary</p>
      <p class="line">
        <svg viewBox="0 0 12 12" aria-hidden="true"><path fill="#1ea4e0" d="M2.5 1l2 2.2-1 1.2a7 7 0 0 0 4.1 4.1l1.2-1 2.2 2-1.3 1.5C5 10.5 1.5 7 1 2.3z"/></svg>
        +36 30 518 2769
      </p>
      <p class="line">
        <svg viewBox="0 0 12 12" aria-hidden="true"><rect x="1" y="2.5" width="10" height="7" fill="#1ea4e0"/><path d="M1 2.5l5 4 5-4" stroke="#1b1b1d" stroke-width="1" fill="none"/></svg>
        b.tolnavari@quindor.hu
      </p>
      <p class="line">
        <svg viewBox="0 0 12 12" aria-hidden="true"><g fill="none" stroke="#1ea4e0" stroke-width="1.1"><circle cx="6" cy="6" r="4.8"/><ellipse cx="6" cy="6" rx="2" ry="4.8"/><path d="M1.2 6h9.6"/></g></svg>
        www.quindor.hu
      </p>
    </div>
  </section>
</body>
</html>
```